Website for 3d printing & other services

Hi, i'm after a website to sell my 3d printed automotive parts as well as sell my 3d printing services & other services.

There's a few things i need the website to have:

- Automatic 3d print quoting based on the file the client uploads to the website.
- Shop function where i can sell my custom automotive parts
- 3D printing technologies offered are SLA & FDM
- My business can offer 3d printing, 3d scanning, 3d cad design, cnc machining, steel fabrication, drafting services.

The color design is to suit my logo which is Black, orange & white.

Target Market(s)

3d printing, automotive, fabrication

Industry/Entity Type

General manufacturing & Custom automotive parts

Coding

Coded - Design and coding required

Number of Pages Required

5+ page

Requirements
Must have
• Automatic 3d print quoting. Shop for my printed parts.

```html
<!DOCTYPE html>
<html lang="en">
<head>
<meta charset="utf-8">
<title>Ravik Draft &amp; Design</title>
<link href="https://fonts.googleapis.com/css2?family=Montserrat:wght@500;600;700&family=Lato:wght@400;700&display=swap" rel="stylesheet">
<style>
:root{
  --orange:#ff7200;
  --orange-dark:#e86400;
  --black:#000;
  --ink:#111;
  --white:#fff;
  --grey-bg:#f3f3f3;
  --footer:#141414;
  --line:#ff9a4a;
}
*{box-sizing:border-box;margin:0;padding:0}
html,body{width:1200px;height:3278px;overflow:hidden}
body{position:relative;background:var(--white);font-family:'Lato',sans-serif;color:var(--ink)}
.abs{position:absolute}
.head-font{font-family:'Montserrat',sans-serif}

/* hero */
.hero{left:0;top:0;width:1200px;height:725px;overflow:hidden}
.hero-photo{position:absolute;inset:0;background:
  radial-gradient(ellipse 260px 200px at 830px 430px,rgba(240,90,60,.55),transparent 70%),
  radial-gradient(ellipse 520px 220px at 900px 330px,rgba(70,200,230,.55),transparent 70%),
  linear-gradient(120deg,#0f1d2a 0%,#183448 40%,#1d4b5e 60%,#3a1c18 85%,#5a2a18 100%)}
.hero-shade{position:absolute;inset:0;background:linear-gradient(90deg,rgba(0,0,0,.6) 0%,rgba(0,0,0,.25) 55%,rgba(0,0,0,0) 100%)}
.topbar{left:490px;top:0;width:710px;height:51px;background:var(--orange);clip-path:polygon(0 0,100% 0,100% 100%,28px 100%)}
.topbar span{position:absolute;top:16px;font:700 14px 'Montserrat',sans-serif;color:var(--white)}
.topbar svg{position:absolute;top:15px}
.topbar .sep{position:absolute;top:14px;width:1px;height:20px;background:var(--line)}
.navband{left:0;top:51px;width:1200px;height:74px;background:rgba(0,0,0,.45)}
.logo{left:110px;top:20px;width:150px;color:var(--white);font:700 26px/1.05 'Montserrat',sans-serif;display:flex;flex-direction:column;align-items:flex-start}
.logo .mark{width:40px;height:40px;border-radius:50%;background:var(--orange);margin-bottom:8px}
.logo small{font-size:15px;letter-spacing:.3px}
.nav a{position:absolute;top:79px;font:500 14.5px 'Montserrat',sans-serif;color:var(--white);text-decoration:none}
.nav a.active{color:var(--orange);text-decoration:underline;text-underline-offset:3px}
.welcome{left:114px;top:290px;font:500 27px 'Montserrat',sans-serif;color:var(--white)}
.hero-title{left:111px;top:338px;font:700 43px 'Montserrat',sans-serif;color:var(--white);letter-spacing:.5px}
.hero-text{left:111px;top:407px;width:400px;font:15px/25.5px 'Lato',sans-serif;color:var(--white)}
.btn-light{left:111px;top:505px;width:186px;height:50px;border-radius:25px;background:var(--white);color:var(--orange);font:500 17px/50px 'Montserrat',sans-serif;text-align:center}

/* headings */
.sec-title{left:0;width:1200px;text-align:center;font:700 31px 'Montserrat',sans-serif;color:var(--ink)}
.sec-title em{font-style:normal;color:var(--orange)}

/* parts */
.part{top:869px;width:222px;height:264px;border-radius:22px}
.arrow{width:32px;height:32px;border-radius:50%;background:var(--black)}
.arrow svg{display:block}
.btn-grad{height:51px;border-radius:26px;background:linear-gradient(90deg,#1a1a1a 0%,#5a2a00 45%,var(--orange) 100%);color:var(--white);font:600 17px/51px 'Montserrat',sans-serif;text-align:center}

/* tech */
.sla{left:0;top:1308px;width:647px;height:406px;background:var(--orange);clip-path:polygon(0 0,100% 0,563px 100%,0 100%)}
.fdm{left:552px;top:1360px;width:648px;height:405px;background:var(--black);clip-path:polygon(82px 0,100% 0,100% 100%,0 100%)}
.tech-title{font:600 29px 'Montserrat',sans-serif;color:var(--white)}
.tech-text{font:15px/25.7px 'Lato',sans-serif;color:var(--white)}

/* services */
.card{top:1911px;width:295px;height:371px;background:var(--black);border-radius:22px}
.card .img{position:absolute;left:12px;top:14px;width:271px;height:283px;border-radius:18px}
.card .label{position:absolute;left:0;top:320px;width:295px;text-align:center;font:500 22px 'Montserrat',sans-serif;color:var(--white)}

/* quote */
.quote{left:0;top:2364px;width:1200px;height:634px;background:var(--grey-bg)}
.field{height:68px;border:1.5px solid var(--orange);background:var(--white);font:700 15px 'Lato',sans-serif;color:#222;padding:24px 0 0 24px}

/* footer */
.footer{left:0;top:2998px;width:1200px;height:280px;background:var(--footer)}
.flogo{left:110px;top:3060px;color:var(--white);font:700 40px/1.05 'Montserrat',sans-serif}
.flogo .mark{width:56px;height:56px;border-radius:50%;background:var(--orange);margin-bottom:10px}
.flogo small{display:block;font-size:22px}
.fnav a{position:absolute;top:3059px;font:500 16px 'Montserrat',sans-serif;color:var(--white);text-decoration:none}
.fline{font:14px 'Lato',sans-serif;color:var(--white)}
.social{top:3201px;width:26px;height:26px;border-radius:50%;background:var(--white)}
</style>
</head>
<body>

<!-- HERO -->
<section class="abs hero">
  <div class="hero-photo" role="img" aria-label="Close-up of a 3D printer nozzle printing an orange and grey gear under cyan light"></div>
  <div class="hero-shade"></div>
</section>

<div class="abs topbar">
  <svg style="left:44px" width="18" height="18" viewBox="0 0 24 24"><path fill="#fff" d="M6.6 10.8a15 15 0 0 0 6.6 6.6l2.2-2.2a1 1 0 0 1 1-.25 11.4 11.4 0 0 0 3.6.57 1 1 0 0 1 1 1V20a1 1 0 0 1-1 1A17 17 0 0 1 3 4a1 1 0 0 1 1-1h3.5a1 1 0 0 1 1 1c0 1.25.2 2.45.57 3.6a1 1 0 0 1-.25 1z"/></svg>
  <i class="sep" style="left:80px"></i>
  <span style="left:100px">CALL:+1 555 010 4477</span>
  <svg style="left:278px" width="18" height="15" viewBox="0 0 24 18"><path fill="#fff" d="M0 0h24v18H0z"/><path fill="none" stroke="#ff7200" stroke-width="2" d="M1 1l11 9 11-9"/></svg>
  <i class="sep" style="left:315px"></i>
  <span style="left:336px">MAIL:INFO@RAVIKDRAFT.COM</span>
</div>

<div class="abs navband"></div>
<div class="abs logo"><i class="mark"></i>RAVIK<small>DRAFT &amp; DESIGN</small></div>
<nav class="nav">
  <a class="active" style="left:461px">HOME</a>
  <a style="left:550px">ABOUT US</a>
  <a style="left:668px">SERVICES</a>
  <a style="left:781px">TESTIMONIALS</a>
  <a style="left:930px">BLOG</a>
  <a style="left:1014px">CONTACT US</a>
</nav>

<div class="abs welcome">WELCOME TO</div>
<h1 class="abs hero-title">RAVIK DRAFT &amp; DESIGN</h1>
<p class="abs hero-text">Itaque earum rerum hic tenetur a sapiente delectus, ut aut reiciendis voluptatibus maiores alias consequatur aut perferendis doloribus asperiores repellat.</p>
<div class="abs btn-light">GET STARTED</div>

<!-- PARTS -->
<h2 class="abs sec-title" style="top:793px">MY CUSTOM <em>AUTOMOTIVE PARTS</em></h2>
<div class="abs arrow" style="left:34px;top:985px"><svg width="32" height="32"><path d="M19 10l-6 6 6 6" stroke="#fff" stroke-width="2.5" fill="none"/></svg></div>
<div class="abs part" style="left:111px;background:linear-gradient(160deg,#3a3a3a,#cfcfcf 55%,#8a8a8a)" role="img" aria-label="Grey 3D printed boat model under an orange printer head"></div>
<div class="abs part" style="left:363px;background:linear-gradient(170deg,#1d2a3a,#6a7c90 50%,#a88a5c)" role="img" aria-label="CNC machine cutting a metal part"></div>
<div class="abs part" style="left:615px;background:linear-gradient(100deg,#d8d8d8,#e96a5a 40%,#cfd3d8)" role="img" aria-label="Hand-held 3D scanner over a red engine block"></div>
<div class="abs part" style="left:866px;background:linear-gradient(160deg,#2a3340,#8a5a3a 45%,#b8b8b8)" role="img" aria-label="Robotic arms welding a car body on a factory line"></div>
<div class="abs arrow" style="left:1130px;top:985px"><svg width="32" height="32"><path d="M13 10l6 6-6 6" stroke="#fff" stroke-width="2.5" fill="none"/></svg></div>
<div class="abs btn-grad" style="left:534px;top:1183px;width:186px">SHOP NOW</div>

<!-- TECHNOLOGIES -->
<div class="abs sla"></div>
<div class="abs fdm"></div>
<h3 class="abs tech-title" style="left:111px;top:1359px">SLA</h3>
<p class="abs tech-text" style="left:111px;top:1410px;width:445px">Nam libero tempore, cum soluta nobis est eligendi optio cumque nihil impedit quo minus id quod maxime placeat facere possimus, omnis voluptas assumenda est, omnis dolor repellendus. Temporibus autem quibusdam et aut officiis debitis aut rerum necessitatibus saepe eveniet ut et voluptates repudiandae sint et molestiae non recusandae.<br><br>Itaque earum rerum hic tenetur a sapiente delectus, ut aut reiciendis voluptatibus maiores alias consequatur aut perferendis doloribus asperiores repellat.</p>
<h3 class="abs tech-title" style="left:900px;top:1410px;width:190px;text-align:right">FDM</h3>
<p class="abs tech-text" style="left:648px;top:1467px;width:441px;text-align:right">Cum soluta nobis est eligendi optio cumque nihil impedit quo minus id quod maxime placeat facere possimus, omnis voluptas assumenda est, omnis dolor repellendus. Temporibus autem quibusdam et aut officiis debitis aut rerum necessitatibus saepe eveniet ut et voluptates repudiandae sint et molestiae non recusandae.<br><br>Itaque earum rerum hic tenetur a sapiente delectus, ut aut reiciendis voluptatibus maiores alias consequatur aut perferendis doloribus asperiores repellat.</p>

<!-- SERVICES -->
<h2 class="abs sec-title" style="top:1834px">OUR <em>SERVICES</em></h2>
<div class="abs arrow" style="left:34px;top:2027px"><svg width="32" height="32"><path d="M19 10l-6 6 6 6" stroke="#fff" stroke-width="2.5" fill="none"/></svg></div>
<div class="abs card" style="left:111px"><div class="img" style="background:linear-gradient(160deg,#7aa0b8,#e6b890 45%,#ff7a2a 75%,#2a2a2a)" role="img" aria-label="Engineer inspecting an orange 3D printed part"></div><div class="label">3D PRINTING</div></div>
<div class="abs card" style="left:452px"><div class="img" style="background:radial-gradient(circle at 55% 55%,#2f5cff 0%,#1a2f8a 35%,#1a1f28 75%)" role="img" aria-label="Blue wireframe CAD model of gears"></div><div class="label">3D CAD DESIGN</div></div>
<div class="abs card" style="left:793px"><div class="img" style="background:linear-gradient(170deg,#8a9a8a,#dcdcd8 50%,#e0c070 90%)" role="img" aria-label="Hands drafting technical plans with a compass"></div><div class="label">DRAFTING SERVICES</div></div>
<div class="abs arrow" style="left:1130px;top:2027px"><svg width="32" height="32"><path d="M13 10l6 6-6 6" stroke="#fff" stroke-width="2.5" fill="none"/></svg></div>

<!-- QUOTE -->
<section class="abs quote"></section>
<h2 class="abs sec-title" style="top:2425px">GET A <em>QUOTE</em></h2>
<div class="abs field" style="left:111px;top:2480px;width:469px">Name</div>
<div class="abs field" style="left:617px;top:2480px;width:469px">Email</div>
<div class="abs field" style="left:111px;top:2567px;width:469px">Phone Number</div>
<div class="abs field" style="left:617px;top:2567px;width:469px">Address</div>
<div class="abs field" style="left:111px;top:2653px;width:977px;height:159px">Message</div>
<div class="abs btn-grad" style="left:519px;top:2867px;width:157px">SUBMIT</div>

<!-- FOOTER -->
<footer class="abs footer"></footer>
<div class="abs flogo"><div class="mark"></div>RAVIK<small>DRAFT &amp; DESIGN</small></div>
<nav class="fnav">
  <a style="left:447px">HOME</a>
  <a style="left:557px">ABOUT</a>
  <a style="left:674px">SERVICES</a>
  <a style="left:812px">BLOG</a>
  <a style="left:919px">CONTACT US</a>
</nav>
<div class="abs fline" style="left:447px;top:3105px;display:flex;align-items:center;gap:8px">
  <svg width="13" height="13" viewBox="0 0 24 24"><path fill="#fff" d="M6.6 10.8a15 15 0 0 0 6.6 6.6l2.2-2.2a1 1 0 0 1 1-.25 11.4 11.4 0 0 0 3.6.57 1 1 0 0 1 1 1V20a1 1 0 0 1-1 1A17 17 0 0 1 3 4a1 1 0 0 1 1-1h3.5a1 1 0 0 1 1 1c0 1.25.2 2.45.57 3.6a1 1 0 0 1-.25 1z"/></svg>
  PHONE : +1 555 010 4477 <span style="margin:0 14px">|</span>
  <svg width="14" height="11" viewBox="0 0 24 18"><path fill="#fff" d="M0 0h24v18H0z"/><path fill="none" stroke="#141414" stroke-width="2" d="M1 1l11 9 11-9"/></svg>
  EMAIL : INFO@RAVIKDRAFT.COM
</div>
<div class="abs fline" style="left:447px;top:3152px;font-size:13px">COPYRIGHTS@2023.RAVIK DRAFT &amp; DESIGN.ALL RIGHTS RESERVED</div>
<div class="abs social" style="left:447px"></div>
<div class="abs social" style="left:493px"></div>
<div class="abs social" style="left:539px"></div>
<div class="abs social" style="left:584px"></div>

</body>
</html>
```